Maple Grove Schools | brand new stationery!

We need stationery design with our new logo! Our company updated it's name and image and we like to incorporate the new one on our stationery, business cards and email signature. We are looking for fresh, new ideas!
Industry: Childcare, Elementary and Middle School
Company Name: Maple Grove Schools
Tagline: Bright Futures Start Here
Main colors: Blue, white and a little yellow
Star shape is something new for us! Do you see a way to incorporate it as a design element?

```html
<!DOCTYPE html>
<html lang="en">
<head>
<meta charset="utf-8">
<title>Maple Grove Schools Stationery</title>
<link href="https://fonts.googleapis.com/css2?family=Poppins:wght@500&family=Noto+Serif:wght@400;700&display=swap" rel="stylesheet">
<style>
  :root {
    --navy: #041c6e;
    --yellow: #f5b800;
    --ink: #1c1c22;
    --paper: #ffffff;
    --backdrop: #dadada;
    --ghost: #ececec;
  }
  html, body { margin: 0; padding: 0; overflow: hidden; }
  body { width: 1200px; height: 749px; background: var(--backdrop); position: relative; font-family: "Noto Serif", serif; }
  .sheet { position: absolute; background: var(--paper); box-shadow: 1px 1px 1px rgba(0,0,0,.35); overflow: hidden; }
  .wordmark { font-family: "Poppins", sans-serif; font-weight: 500; color: var(--ink); white-space: nowrap; }
  .wordmark-dot { display: inline-block; border-radius: 50%; background: var(--navy); vertical-align: middle; }
  .band { position: absolute; left: 0; right: 0; background: var(--navy); border-top: 2px solid var(--yellow); color: #fff; }

  /* Letterhead */
  .letterhead { left: 388px; top: 133px; width: 371px; height: 479px; }
  .letterhead-brand { position: absolute; top: 146px; left: 0; right: 0; text-align: center; font-size: 15.5px; }
  .letterhead-brand .wordmark-dot { width: 18px; height: 18px; margin-right: 7px; }
  .letterhead-ghost { position: absolute; left: 146px; top: 166px; width: 118px; height: 118px; border-radius: 50%; background: var(--ghost); }
  .letterhead .band { top: 443px; height: 34px; text-align: center; font-size: 7.8px; }
  .letterhead-address { margin-top: 4px; }
  .letterhead-rule { width: 288px; height: 0; border-top: 0.6px solid #fff; margin: 3px auto 3px; }
  .letterhead-contacts b { color: var(--yellow); }
  .letterhead-contacts .sep { margin: 0 5px; }

  /* Business card */
  .card { left: 161px; top: 335px; width: 347px; height: 105px; z-index: 2; }
  .card-person { position: absolute; left: 18px; top: 20px; }
  .card-name { font-family: "Poppins", sans-serif; font-weight: 500; color: var(--navy); font-size: 9px; line-height: 10px; }
  .card-title { font-size: 6.6px; color: var(--ink); line-height: 9px; }
  .card-contacts { list-style: none; margin: 6px 0 0; padding: 0; font-size: 6.6px; color: var(--ink); }
  .card-contacts li { display: flex; align-items: center; height: 9.2px; }
  .card-contacts svg { width: 7px; height: 7px; margin-right: 4px; }
  .card-brand { position: absolute; right: 22px; top: 32px; width: 110px; text-align: center; font-size: 13px; line-height: 13px; }
  .card-brand .wordmark-dot { width: 14px; height: 14px; margin-bottom: 6px; }
  .card .band { top: 86px; height: 17px; font-size: 6.8px; font-weight: 700; padding-left: 22px; line-height: 17px; }

  /* Envelope */
  .envelope { left: 800px; top: 231px; width: 295px; height: 304px; }
  .envelope-brand { position: absolute; left: 14px; top: 10px; font-size: 10.8px; }
  .envelope-brand .wordmark-dot { width: 14px; height: 14px; margin-right: 5px; }
  .envelope .band { top: 126px; height: 19px; font-size: 6.2px; padding-left: 14px; line-height: 19px; }
  .envelope-flap { position: absolute; left: 0; top: 157px; width: 295px; height: 35px; }
</style>
</head>
<body>

<section class="sheet letterhead">
  <div class="letterhead-brand wordmark"><span class="wordmark-dot"></span>Maple Grove Schools</div>
  <div class="letterhead-ghost" role="img" aria-label="Faint background brand shape"></div>
  <div class="band">
    <div class="letterhead-address">Your Address line here, Country Code 0123456</div>
    <div class="letterhead-rule"></div>
    <div class="letterhead-contacts"><b>P:</b> 044-987 654 321<span class="sep">|</span><b>E:</b> hello@maplegrove.com<span class="sep">|</span><b>W:</b> www.maplegrove.com</div>
  </div>
</section>

<section class="sheet card">
  <div class="card-person">
    <div class="card-name">Daniel Reyes</div>
    <div class="card-title">Managing Director</div>
    <ul class="card-contacts">
      <li><svg viewBox="0 0 10 10"><rect x="0.6" y="0.6" width="8.8" height="8.8" fill="none" stroke="#041c6e" stroke-width="1"/><path d="M3 2.5 L4 2.3 L4.6 3.8 L3.9 4.3 Q4.6 5.8 5.8 6.2 L6.3 5.5 L7.6 6.1 L7.4 7.2 Q4 7.5 3 2.5Z" fill="#041c6e"/></svg>044-987 654 321</li>
      <li><svg viewBox="0 0 10 10"><rect x="0.5" y="2" width="9" height="6.5" fill="#041c6e"/><path d="M0.5 2 L5 6 L9.5 2" fill="none" stroke="#fff" stroke-width="0.8"/></svg>hello@maplegrove.com</li>
      <li><svg viewBox="0 0 10 10"><circle cx="5" cy="5" r="4.3" fill="none" stroke="#041c6e" stroke-width="0.9"/><ellipse cx="5" cy="5" rx="1.8" ry="4.3" fill="none" stroke="#041c6e" stroke-width="0.8"/><path d="M0.7 5 H9.3 M1.5 3 H8.5 M1.5 7 H8.5" stroke="#041c6e" stroke-width="0.7"/></svg>www.maplegrove.com</li>
    </ul>
  </div>
  <div class="card-brand wordmark"><span class="wordmark-dot"></span><br>Maple Grove<br>Schools</div>
  <div class="band">Your Address line here, Country Code 0123456</div>
</section>

<section class="sheet envelope">
  <div class="envelope-brand wordmark"><span class="wordmark-dot"></span>Maple Grove Schools</div>
  <div class="band">Your Address line here, Country Code 0123456</div>
  <svg class="envelope-flap" viewBox="0 0 295 35" preserveAspectRatio="none"><polygon points="0,0 295,0 283,35 11,35" fill="#041c6e"/></svg>
</section>

</body>
</html>
```